Business Card Design - Amberfield Court

We are looking at a new design for our business cards that has a modern and professional look. We run a residential aged care facility focussing on the care of residents. The cards will be used for potential clients, consultants and business opportunities in this sector. Blue and white is our main colours and would to see these colours incorporated in the design.
Industry/Entity Type
Business
Contact Information for Business Card
Amberfield Court, Darren Walsh, dwalsh@amberfieldcourt.com.au, Finance Manager, 0472 639 208, BCom, 37 Marrabel Crescent, Brindle Vale, Qld 4093.
Look and feel
Each slider illustrates characteristics of the customer's brand and the style your logo design should communicate.

```html
<!DOCTYPE html>
<html lang="en">
<head>
<meta charset="utf-8">
<title>Amberfield Court – Business Card</title>
<link href="https://fonts.googleapis.com/css2?family=Montserrat:wght@700&family=Open+Sans:wght@400;600&display=swap" rel="stylesheet">
<style>
  :root {
    --navy: #1f3d4e;
    --steel: #4a7d9b;
    --white: #ffffff;
    --ink: #2a3a44;
    --stage: #d9dde0;
  }
  * { margin: 0; padding: 0; box-sizing: border-box; }
  html, body { width: 1200px; height: 900px; overflow: hidden; background: var(--stage); }
  .canvas { position: relative; width: 1200px; height: 900px; }
  .card {
    position: absolute; left: 270px; width: 660px; height: 377px;
    border-radius: 22px; overflow: hidden;
  }
  .card-back { top: 50px; background: var(--navy); }
  .card-front { top: 473px; background: var(--white); }
  .card-front .waves { position: absolute; inset: 0; }

  .brand {
    position: absolute; display: flex; align-items: center; gap: 14px;
    font-family: "Open Sans", sans-serif; font-weight: 600; color: var(--white);
    letter-spacing: 2px; text-transform: uppercase; white-space: nowrap;
  }
  .brand-dot { border-radius: 50%; background: var(--steel); flex: none; }
  .card-back .brand { left: 50%; top: 50%; transform: translate(-50%, -50%); font-size: 30px; }
  .card-back .brand-dot { width: 46px; height: 46px; }

  .card-front .brand {
    right: 36px; top: 140px; width: 140px;
    flex-direction: column; gap: 10px; text-align: center;
    font-size: 17px; line-height: 1.25; white-space: normal;
  }
  .card-front .brand-dot { width: 30px; height: 30px; background: var(--white); }

  .contact { position: absolute; left: 58px; top: 150px; font-family: "Open Sans", sans-serif; color: var(--ink); }
  .contact-name { font-family: "Montserrat", sans-serif; font-weight: 700; font-size: 27px; color: var(--navy); letter-spacing: 0.5px; line-height: 1.1; }
  .contact-role { font-size: 13px; color: var(--steel); text-transform: uppercase; margin-bottom: 12px; }
  .contact-line { display: flex; align-items: center; gap: 7px; font-size: 15px; line-height: 1.45; }
  .contact-line svg { width: 13px; height: 13px; fill: var(--steel); flex: none; }
  .contact-address { font-size: 15px; line-height: 1.3; margin-top: 10px; }
</style>
</head>
<body>
<main class="canvas">
  <section class="card card-back">
    <div class="brand"><span class="brand-dot"></span>Amberfield Court</div>
  </section>

  <section class="card card-front">
    <svg class="waves" viewBox="0 0 660 377" aria-hidden="true">
      <path d="M660 42 C530 42 455 105 424 200 C398 282 362 322 270 331 C170 340 80 340 0 338" fill="none" stroke="var(--navy)" stroke-width="9"/>
      <path d="M660 60 C540 60 470 120 440 210 C415 290 380 335 280 345 C180 352 90 352 0 350 L0 377 L660 377 Z" fill="var(--steel)"/>
      <path d="M0 362 C200 358 420 366 660 358 L660 377 L0 377 Z" fill="var(--navy)"/>
    </svg>

    <div class="brand"><span class="brand-dot"></span>Amberfield Court</div>

    <div class="contact">
      <div class="contact-name">DARREN WALSH</div>
      <div class="contact-role">Finance Manager (BCom)</div>
      <div class="contact-line">
        <svg viewBox="0 0 24 24"><path d="M6.6 10.8a15 15 0 0 0 6.6 6.6l2.2-2.2a1 1 0 0 1 1-.25 11.4 11.4 0 0 0 3.6.57 1 1 0 0 1 1 1V20a1 1 0 0 1-1 1A17 17 0 0 1 3 4a1 1 0 0 1 1-1h3.5a1 1 0 0 1 1 1c0 1.25.2 2.45.57 3.57a1 1 0 0 1-.25 1z"/></svg>
        0472 639 208
      </div>
      <div class="contact-line">
        <svg viewBox="0 0 24 24"><path d="M2 5h20v14H2z M4 7v.5l8 5 8-5V7l-8 5z" fill-rule="evenodd"/></svg>
        dwalsh@amberfieldcourt.com.au
      </div>
      <div class="contact-address">37 Marrabel Crescent<br>Brindle Vale, Qld 4093</div>
    </div>
  </section>
</main>
</body>
</html>
```